business card deign

Logo needs the following on it.
1. attached logo
2. Tagline - "Cold drinks, good company and a party that never stops!"
3. Name- Dalton Pikes, Founder and CPO
4. Address - 412 E. Carver Avenue, Ste 2207, Tampa, FL. 33917
5. Phone - 555.318.4726

```html
<!DOCTYPE html>
<html lang="en">
<head>
<meta charset="utf-8">
<title>Briska business card</title>
<link rel="stylesheet" href="https://fonts.googleapis.com/css2?family=Arimo:wght@700&family=Open+Sans:wght@400;600&display=swap">
<style>
  :root {
    --stage: #232323;
    --card-black: #0f0f0f;
    --card-dark: #151515;
    --paper: #ffffff;
    --rim: #9b9da1;
    --ink: #000000;
    --muted: #e6e6e6;
  }
  * { box-sizing: border-box; margin: 0; padding: 0; }
  html, body { width: 1200px; height: 711px; overflow: hidden; }
  body {
    background: var(--stage);
    display: flex;
    align-items: center;
    justify-content: center;
    gap: 40px;
    font-family: "Open Sans", sans-serif;
  }
  .card {
    position: relative;
    width: 540px;
    height: 309px;
    border-radius: 24px;
    overflow: hidden;
    box-shadow: 0 14px 30px rgba(0,0,0,.55);
  }
  .card--front {
    background: var(--card-black);
    display: flex;
    align-items: center;
    justify-content: center;
  }
  .wordmark {
    display: flex;
    align-items: center;
    gap: 16px;
    font-family: "Arimo", sans-serif;
    font-weight: 700;
    letter-spacing: 14px;
    white-space: nowrap;
  }
  .wordmark__dot { width: 26px; height: 26px; border-radius: 50%; flex: none; }
  .card--front .wordmark { color: var(--paper); font-size: 40px; }
  .card--front .wordmark__dot { background: var(--paper); }

  .card--back { background: var(--card-dark); }
  .back__disc { position: absolute; inset: 0; }
  .back__brand {
    position: absolute;
    right: 14px;
    top: 92px;
    width: 250px;
    display: flex;
    justify-content: center;
  }
  .card--back .wordmark { color: var(--ink); font-size: 26px; letter-spacing: 8px; gap: 12px; }
  .card--back .wordmark__dot { background: var(--ink); width: 18px; height: 18px; }

  .person {
    position: absolute;
    left: 0;
    top: 44px;
    display: flex;
    align-items: stretch;
    gap: 12px;
  }
  .person__bar { width: 22px; background: var(--paper); }
  .person__name {
    font-family: "Arimo", sans-serif;
    font-weight: 700;
    font-size: 25px;
    color: var(--paper);
    line-height: 1.1;
  }
  .person__role { font-size: 15px; font-weight: 600; color: var(--paper); margin-top: 4px; }

  .details {
    position: absolute;
    left: 34px;
    bottom: 28px;
    color: var(--muted);
    font-size: 14px;
    line-height: 1.35;
  }
  .tagline { margin-bottom: 16px; width: 215px; }
  .contact { list-style: none; }
  .contact li { display: flex; gap: 8px; align-items: flex-start; }
  .contact svg { width: 13px; height: 13px; margin-top: 3px; flex: none; fill: var(--muted); }
</style>
</head>
<body>
  <section class="card card--front" aria-label="Card front">
    <div class="wordmark"><span class="wordmark__dot"></span>BRISKA</div>
  </section>

  <section class="card card--back" aria-label="Card back">
    <svg class="back__disc" viewBox="0 0 540 309" aria-hidden="true">
      <circle cx="462" cy="26" r="234" fill="var(--rim)"/>
      <circle cx="472" cy="18" r="230" fill="var(--paper)"/>
    </svg>
    <div class="back__brand">
      <div class="wordmark"><span class="wordmark__dot"></span>BRISKA</div>
    </div>

    <div class="person">
      <span class="person__bar"></span>
      <div>
        <p class="person__name">Dalton Pikes</p>
        <p class="person__role">Founder and CPO</p>
      </div>
    </div>

    <div class="details">
      <p class="tagline">Cold drinks, good company and a party that never stops!</p>
      <ul class="contact">
        <li>
          <svg viewBox="0 0 24 24"><path d="M6.6 10.8a15.1 15.1 0 0 0 6.6 6.6l2.2-2.2a1 1 0 0 1 1-.25 11.4 11.4 0 0 0 3.6.6 1 1 0 0 1 1 1V20a1 1 0 0 1-1 1A17 17 0 0 1 3 4a1 1 0 0 1 1-1h3.5a1 1 0 0 1 1 1c0 1.25.2 2.45.6 3.6a1 1 0 0 1-.25 1z"/></svg>
          <span>555.318.4726</span>
        </li>
        <li>
          <svg viewBox="0 0 24 24"><path d="M12 2a7 7 0 0 0-7 7c0 5.250 7 13 7 13s7-7.75 7-13a7 7 0 0 0-7-7zm0 9.5A2.5 2.5 0 1 1 12 6.5a2.5 2.5 0 0 1 0 5z"/></svg>
          <span>412 E. Carver Avenue,<br>Ste 2207, Tampa, FL. 33917</span>
        </li>
      </ul>
    </div>
  </section>
</body>
</html>
```